Refer a friend or family in July 2014

We offer the following classrooms to suit ALL your needs.

Please put in table or in a clear format so parents can read this information

Before school care $35 or after rebates $17.50 per morning
Long day / vacation care $110 per day or after rebates $55.00 per day
Early morning Half day / vacation care (6.00am to 2.30pm) $80 per day or after rebates $40 per day
Half day / vacation care $60 per day (8.30am to 2.00pm) or after rebates $30 per day Vacation care half day 6am to 12pm or 12pm to 5.30pm $55 or $27.50 after rebates
After school care $45.00 or after rebate $22.50 per day

* Terms and Conditions – Family Referral Form
1. Offer valid till 31 August 2014
2. New Child must be enrolled for a minimum of 2 days per week and a 4 week period minimum before credit is applied
3. The $50 account credit will be added 5 weeks after referring family/families have started at Gathering Sprouts Dotted Otters Junior Education Centre.
4. The credit cannot be refunded as cash and is only a credit on their current account.
5. Discount offer applies only to all new referred children.
6. Existing children enrolled or siblings of current families at the centre are not eligible for this offer.

Target Market(s)

parents

Industry/Entity Type

School

Font styles to use
Sans Serif

Requirements
Must have
• refer a friend or family in July !

childcare local to you.

children learn, laugh and have fun!

be professional and corporate over "colourful and too childcare like " this is for parents

flexible times to suit you.

qualified teachers

get ready for school program - pre -kindergarten classroom

www.gatheringsprouts-demo.com.au

0491736258
Should not have
• too much colour to messy - unclear..

```html
<!DOCTYPE html>
<html lang="en">
<head>
<meta charset="utf-8">
<title>Refer a friend or family in July</title>
<link rel="stylesheet" href="https://fonts.googleapis.com/css2?family=Overlock:ital,wght@0,400;1,400;1,700&family=Open+Sans:ital,wght@0,400;1,400;1,600&display=swap">
<style>
  :root {
    --green: #6f9a2e;
    --purple: #5a3a8c;
    --purple-deep: #3d2468;
    --lilac: #c9b6e0;
    --lilac-soft: #e9e1f3;
    --grey-band: #e4e4e6;
    --ink: #1d1d22;
    --white: #ffffff;
    --page: #eeeeee;
  }
  html, body { margin: 0; padding: 0; }
  body {
    width: 1200px; height: 1135px; overflow: hidden;
    background: var(--page);
    position: relative;
  }
  .flyer {
    position: absolute; left: 205px; top: 19px;
    width: 688px; height: 955px;
    background: var(--white);
    transform: scale(1.148); transform-origin: 0 0;
    overflow: hidden;
    font-family: "Open Sans", Arial, sans-serif;
    box-shadow: 0 4px 18px rgba(0,0,0,.18);
  }
  .flyer > * { position: absolute; }
  .header-band { left: 0; top: 0; width: 688px; height: 206px; background: var(--green); }
  .grey-band { left: 0; top: 206px; width: 688px; height: 164px; background: var(--grey-band); }
  .bubble-tail { left: 0; top: 369px; }
  .headline {
    left: 0; top: 8px; width: 688px; margin: 0; text-align: center;
    font-family: "Overlock", Georgia, sans-serif; font-style: italic; font-weight: 400;
    font-size: 47px; color: var(--white); letter-spacing: .3px;
    text-shadow: 0 2px 3px rgba(0,0,0,.25);
  }
  .hero-photo {
    left: 30px; top: 72px; width: 627px; height: 239px;
    background: radial-gradient(ellipse at 50% 45%, #f7f3fb 0%, #d8c9e8 60%, #b9a2d4 100%);
  }
  .hero-shadow {
    left: 40px; top: 308px; width: 607px; height: 14px;
    background: radial-gradient(ellipse at 50% 0%, rgba(0,0,0,.28), rgba(0,0,0,0) 70%);
  }
  .intro {
    left: 0; top: 332px; width: 688px; margin: 0; text-align: center;
    font-family: "Overlock", Georgia, sans-serif; font-style: italic;
    font-size: 19px; color: var(--ink); letter-spacing: .2px;
  }
  .price-list {
    left: 51px; top: 378px; margin: 0; padding: 0; list-style: none;
    font-style: italic; font-weight: 600; font-size: 13.2px; line-height: 21px; color: var(--ink);
  }
  .terms-panel { left: 0; top: 521px; }
  .terms {
    left: 18px; top: 529px; width: 420px; margin: 0;
    font-style: italic; font-size: 12.6px; line-height: 21px; color: var(--white);
  }
  .terms p { margin: 0; }
  .ring { left: 446px; top: 491px; width: 220px; height: 220px; border-radius: 50%; background: var(--lilac-soft); }
  .class-photo {
    left: 458px; top: 503px; width: 196px; height: 196px; border-radius: 50%;
    background: radial-gradient(circle at 50% 55%, #8c7a5e 0%, #4b4a55 55%, #26283a 100%);
    border: 1px solid var(--lilac);
  }
  .features { left: 0; top: 711px; width: 688px; height: 120px; }
  .features .item {
    position: absolute; right: 33px; margin: 0;
    font-family: "Overlock", Georgia, sans-serif; font-style: italic;
    font-size: 14.5px; color: var(--ink); text-align: right; white-space: nowrap;
  }
  .features .rule { position: absolute; height: 1px; background: var(--purple); }
  .play-photo {
    left: 0; top: 793px; width: 688px; height: 132px;
    background: linear-gradient(180deg, #ffffff 0%, #d9dde2 45%, #b9c2cc 100%);
    opacity: .85;
  }
  .centre-name {
    left: 19px; top: 810px; width: 122px; height: 100px; background: var(--purple);
    display: flex; align-items: center; justify-content: center; text-align: center;
    margin: 0; padding: 0 6px; box-sizing: border-box;
    font-size: 11px; line-height: 14px; color: var(--white);
  }
  .phone { left: 355px; top: 860px; display: flex; align-items: center; gap: 10px; }
  .phone-number {
    font-family: "Open Sans", Arial, sans-serif; font-size: 42px; color: var(--purple-deep);
    letter-spacing: .5px; line-height: 1;
  }
  .footer-band {
    left: 0; top: 925px; width: 688px; height: 30px; background: var(--green);
    display: flex; align-items: center; justify-content: center;
    font-family: "Overlock", Georgia, sans-serif; font-size: 17px; letter-spacing: 6.4px;
    color: var(--white);
  }
</style>
</head>
<body>
<main class="flyer">
  <div class="header-band"></div>
  <div class="grey-band"></div>
  <svg class="bubble-tail" width="60" height="40" viewBox="0 0 60 40" aria-hidden="true">
    <polygon points="13,0 46,0 30,37" fill="#e4e4e6"/>
  </svg>

  <h1 class="headline">Refer a friend or family in July !</h1>
  <div class="hero-photo" role="img" aria-label="Photo of a teacher doing crafts with three young children at a table"></div>
  <div class="hero-shadow"></div>

  <p class="intro">We offer the following classrooms to suit ALL your needs.</p>

  <ul class="price-list">
    <li>Before school care $35 or after rebates $17.50 per morning</li>
    <li>Long day / vacation care $110 per day or after rebates $55.00 per day</li>
    <li>Early morning Half day / vacation care (6.00am to 2.30pm) $80 per day or</li>
    <li>after rebates $40 per day</li>
    <li>Half day / vacation care $60 per day (8.30am to 2.00pm) or after rebates $30 per day</li>
    <li>After school care $45.00 or after rebate $22.50 per day</li>
  </ul>

  <svg class="terms-panel" width="688" height="272" viewBox="0 0 688 272" aria-hidden="true">
    <polygon points="0,0 545,0 545,168 408,271 0,271" fill="#5a3a8c"/>
  </svg>
  <div class="ring"></div>
  <div class="class-photo" role="img" aria-label="Photo of children playing in a classroom with a teacher"></div>

  <div class="terms">
    <p>* Terms and Conditions – Family Referral Form</p>
    <p>1. Offer valid till 31 July 2014</p>
    <p>2. New Child must be enrolled for a minimum of 2 days per week and a 4 week period minimum before credit is applied</p>
    <p>3. The $50 account credit will be added 5 weeks after referring family/families have started at Gathering Sprouts Dotted Otters Junior Education Centre.</p>
    <p>4. The credit cannot be refunded as cash and is only a credit on their current account.</p>
    <p>5. Discount offer applies only to all new referred children.</p>
    <p>6. Existing children enrolled or siblings of current families at the centre are not eligible for this offer.</p>
  </div>

  <div class="play-photo" role="img" aria-label="Faded photo of children on an outdoor climbing frame"></div>

  <div class="features">
    <p class="item" style="top:2px">qualified teachers</p>
    <div class="rule" style="left:528px; top:24px; width:134px"></div>
    <svg style="position:absolute; left:659px; top:21px" width="7" height="7" aria-hidden="true"><circle cx="3.5" cy="3.5" r="3" fill="#5a3a8c"/></svg>
    <p class="item" style="top:27px">childcare local to you.</p>
    <div class="rule" style="left:505px; top:49px; width:150px"></div>
    <p class="item" style="top:50px">flexible times to suit you.</p>
    <div class="rule" style="left:480px; top:72px; width:175px"></div>
    <p class="item" style="top:76px">children learn, laugh and have fun!</p>
    <div class="rule" style="left:460px; top:98px; width:195px"></div>
    <p class="item" style="top:101px; right:28px">get ready for school program - pre -kindergarten classroom</p>
  </div>

  <p class="centre-name">Gathering Sprouts Dotted Otters Junior Education Centre</p>

  <div class="phone">
    <svg width="48" height="48" viewBox="0 0 48 48" aria-hidden="true">
      <circle cx="24" cy="24" r="23" fill="#ffffff" stroke="#cfcfd4" stroke-width="1.5"/>
      <path d="M17 12c1.5-1 3-.6 3.8.8l2.2 4c.6 1.1.3 2.3-.7 3l-1.6 1.1c.9 2.6 2.8 5 5.4 6.5l1.2-1.5c.8-.9 2-1.1 3-.5l3.9 2.4c1.3.8 1.6 2.4.6 3.7l-1.3 1.7c-1.4 1.8-3.8 2.2-6 1.1C21.6 33 15.7 26.4 13.6 19.6c-.7-2.3-.1-4.5 1.6-6z" fill="#2a2a30"/>
    </svg>
    <span class="phone-number">0491736258</span>
  </div>

  <div class="footer-band">www.gatheringsprouts-demo.com.au</div>
</main>
</body>
</html>
```